Brightwick Music Studio needs a promotional postcard design

We are looking for a postcard design for a small business that provides clients with private music lesson instruction. We are looking for a design that will convey the message of "music is fun for kids" that will appeal to parents and encourage them to sign up. We have a company logo that should be used and our color scheme is teal and turquoise. All of our contact info should be displayed as well.

Target Market(s)

Parents with young kids

Contact Information for Business Card

web: www.brightwickmusicstudio.example
email: lessons@brightwickmusicstudio.example
phone: 202-555-0147

Font styles to use
Serif
Sans Serif

Colors
33b8a4
86cfc6
0456a4
87cfc6

Requirements
Must have
• Music lessons in your home
• Creating little stars one at a time
• Sign Up Now
• Please use these images:
Nice to have
• Something like this sample postcard:

```html
<!DOCTYPE html>
<html lang="en">
<head>
<meta charset="utf-8">
<title>Brightwick Music Studio – Postcard</title>
<link rel="stylesheet" href="https://fonts.googleapis.com/css2?family=Exo+2:wght@500&family=Libre+Baskerville&family=Open+Sans:wght@700&display=swap">
<style>
  :root {
    --teal: #4fb8bd;
    --teal-deep: #33a6ab;
    --white: #ffffff;
    --paper: #e9ecec;
    --stamp: #dcdcdc;
    --rule: #9a9a9a;
  }
  * { box-sizing: border-box; margin: 0; padding: 0; }
  html, body { width: 1200px; height: 844px; overflow: hidden; }
  body { background: var(--paper); position: relative; }

  .postcard {
    position: absolute;
    width: 560px;
    height: 374px;
    background: var(--white);
    overflow: hidden;
    box-shadow: 0 6px 18px rgba(0,0,0,.18);
  }
  .postcard--front { left: 24px; top: 235px; }
  .postcard--back { left: 616px; top: 235px; }

  .band { position: absolute; inset: 0; width: 560px; height: 374px; }

  .photo {
    position: absolute;
    border: 5px solid var(--white);
    box-shadow: 0 1px 3px rgba(0,0,0,.25);
  }
  .photo--choir { left: 40px; top: 96px; width: 138px; height: 190px;
    background: linear-gradient(160deg, #2a2a2a, #5a4a44 60%, #8a6f5e); }
  .photo--piano { left: 176px; top: 96px; width: 168px; height: 186px; border: none;
    background: linear-gradient(170deg, #0e1630, #1f2a4a 55%, #d9d6dc); }
  .photo--violin-stage { left: 344px; top: 96px; width: 178px; height: 178px; border: none;
    background: linear-gradient(150deg, #3a2a1e, #8a5a34 55%, #b2372c); }
  .photo--smile { left: 40px; top: 105px; width: 148px; height: 140px;
    background: linear-gradient(160deg, #b9a192, #6d5a52 60%, #2c2a30); }
  .photo--violin-solo { left: 214px; top: 40px; width: 112px; height: 160px;
    background: linear-gradient(180deg, #121212, #2b2b2b 65%, #4a8a86); }

  .brand {
    position: absolute;
    display: flex;
    align-items: center;
    gap: 10px;
  }
  .brand--front { left: 320px; top: 24px; }
  .brand__dot { width: 44px; height: 44px; border-radius: 50%; background: var(--teal); flex: none; }
  .brand__name {
    font-family: "Libre Baskerville", Georgia, serif;
    font-size: 18px;
    line-height: 22px;
    color: var(--teal-deep);
    white-space: nowrap;
  }

  .slogan {
    position: absolute;
    left: 60px;
    top: 294px;
    font-family: "Exo 2", "Trebuchet MS", sans-serif;
    font-weight: 500;
    font-size: 27px;
    line-height: 36px;
    color: var(--white);
    letter-spacing: .5px;
  }

  .stamp { position: absolute; left: 450px; top: 18px; width: 70px; height: 58px; background: var(--stamp); }
  .address-lines { position: absolute; left: 360px; top: 92px; width: 180px; }
  .address-lines span { display: block; height: 28px; border-bottom: 1px solid var(--rule); }

  .brand--back { right: 20px; top: 212px; flex-direction: column; gap: 6px; align-items: flex-end; }
  .brand--back .brand__dot { background: var(--white); }
  .brand--back .brand__name { color: var(--white); font-size: 12px; line-height: 16px; }

  .contact {
    position: absolute;
    left: 44px;
    top: 286px;
    list-style: none;
    font-family: "Open Sans", Arial, sans-serif;
    font-weight: 700;
    font-size: 15px;
    line-height: 26px;
    color: var(--white);
  }
</style>
</head>
<body>
  <section class="postcard postcard--front" aria-label="Postcard front">
    <svg class="band" viewBox="0 0 560 374" aria-hidden="true">
      <polygon points="0,232 560,268 560,374 0,374" fill="var(--teal)"/>
    </svg>
    <div class="brand brand--front">
      <span class="brand__dot"></span>
      <span class="brand__name">Brightwick<br>Music Studio</span>
    </div>
    <div class="photo photo--choir" role="img" aria-label="Photo of a group of children singing with their teacher"></div>
    <div class="photo photo--piano" role="img" aria-label="Photo of a young girl playing a grand piano"></div>
    <div class="photo photo--violin-stage" role="img" aria-label="Photo of a child playing violin in a recital hall"></div>
    <p class="slogan">MUSIC IS<br>FUN&nbsp; FOR KIDS</p>
  </section>

  <section class="postcard postcard--back" aria-label="Postcard back">
    <svg class="band" viewBox="0 0 560 374" aria-hidden="true">
      <polygon points="0,250 560,178 560,374 0,374" fill="var(--teal)"/>
    </svg>
    <div class="stamp"></div>
    <div class="address-lines"><span></span><span></span><span></span><span></span></div>
    <div class="photo photo--smile" role="img" aria-label="Photo of a smiling girl at a music lesson"></div>
    <div class="photo photo--violin-solo" role="img" aria-label="Photo of a girl performing violin on stage"></div>
    <div class="brand brand--back">
      <span class="brand__dot"></span>
      <span class="brand__name">Brightwick Music Studio</span>
    </div>
    <ul class="contact">
      <li>P: 202-555-0147</li>
      <li>E: lessons@brightwickmusicstudio.example</li>
      <li>www.brightwickmusicstudio.example</li>
    </ul>
  </section>
</body>
</html>
```